Vitamin B12 Liquid Drops Label

hi, i need a label designed for my vitamin b12 drops that i am going to be selling on shopzello. the label needs to quickly capture the attention of a buyer as he or she is scrolling through the thumbnail search results on shopzello.com my brand is called nralo. i already have an example brand logo i will be using, however, i need help designing the rest of the label. attached are some examples of labels i like for other supplements.some of these examples are pink. i do not want pink. please go for a blue/green color scheme. THE DESIGN MUST BE BOLD

Target Market(s)

adults ages 30 - 64

Font styles to use
Sans Serif

Colors
0455a3
cedeed
3176b5
85acd3
cfdeed
9bcb3b
abd037
cadf82
00a990

Requirements
Must have
• - bold design
• - somewhat gender-neutral color scheme because this will be used equally by men and women
• - B12 MUST be very prominent and visible on the label
Should not have
• - it should not be "crunchy" looking

```html
<!DOCTYPE html>
<html lang="en">
<head>
<meta charset="utf-8">
<title>nralo Vitamin B12 Drops Label</title>
<link rel="stylesheet" href="https://fonts.googleapis.com/css2?family=Montserrat:wght@600;700;800&family=Fredoka:wght@600&display=swap">
<style>
  :root {
    --page-bg: #f2f3f5;
    --label-light: #dfeaf4;
    --label-mid: #b9d0e4;
    --label-deep: #85acd3;
    --brand-purple: #4b2fa0;
    --lime: #b9dc3c;
    --lime-soft: #cadf82;
    --white: #ffffff;
  }
  html, body {
    margin: 0;
    padding: 0;
    width: 1028px;
    height: 1200px;
    overflow: hidden;
    background: var(--page-bg);
  }
  .canvas {
    position: relative;
    width: 1028px;
    height: 1200px;
  }
  .label {
    position: absolute;
    left: 81px;
    top: 47px;
    width: 866px;
    height: 1106px;
    overflow: hidden;
    font-family: "Montserrat", sans-serif;
    box-shadow: 0 4px 18px rgba(0,0,0,0.12);
  }
  .label-art {
    position: absolute;
    inset: 0;
    background:
      radial-gradient(circle at 30% 28%, rgba(255,255,255,0.7), transparent 45%),
      radial-gradient(circle at 75% 75%, rgba(133,172,211,0.55), transparent 50%),
      linear-gradient(180deg, var(--label-light) 0%, var(--label-mid) 60%, var(--label-deep) 100%);
  }
  .brand-name {
    position: absolute;
    top: 26px;
    left: 0;
    right: 0;
    text-align: center;
    font-weight: 800;
    font-size: 64px;
    letter-spacing: 1px;
    color: var(--brand-purple);
    line-height: 72px;
  }
  .product-kicker,
  .product-form {
    position: absolute;
    left: 0;
    right: 0;
    text-align: center;
    font-weight: 600;
    font-size: 90px;
    line-height: 100px;
    color: var(--brand-purple);
    letter-spacing: 1px;
  }
  .product-kicker { top: 148px; }
  .product-form { top: 598px; }
  .product-hero {
    position: absolute;
    top: 210px;
    left: 0;
    right: 0;
    text-align: center;
    font-family: "Fredoka", sans-serif;
    font-weight: 600;
    font-size: 440px;
    line-height: 400px;
    letter-spacing: -18px;
    color: var(--lime);
    -webkit-text-stroke: 12px var(--brand-purple);
    paint-order: stroke fill;
  }
  .supplement-tag {
    position: absolute;
    top: 884px;
    left: 200px;
    width: 466px;
    height: 66px;
    background: var(--lime-soft);
    color: var(--brand-purple);
    font-weight: 600;
    font-size: 32px;
    letter-spacing: 3px;
    line-height: 66px;
    text-align: center;
  }
  .net-volume {
    position: absolute;
    bottom: 0;
    left: 272px;
    width: 322px;
    height: 80px;
    background: var(--brand-purple);
    color: var(--white);
    font-weight: 700;
    font-size: 34px;
    line-height: 80px;
    text-align: center;
    letter-spacing: -0.5px;
  }
</style>
</head>
<body>
  <div class="canvas">
    <section class="label">
      <div class="label-art" role="img" aria-label="Soft blue background with floating translucent cells"></div>
      <div class="brand-name">NRALO</div>
      <div class="product-kicker">VITAMIN</div>
      <div class="product-hero">B12</div>
      <div class="product-form">DROPS</div>
      <div class="supplement-tag">DIETARY SUPPLEMENT</div>
      <div class="net-volume">2 fl oz (60ml)</div>
    </section>
  </div>
</body>
</html>
```